New Zealand Marlborough Sauvignon Blanc wine packaging design

We need packaging design for our new wine brand, Dunmore Vale. The wine is a New Zealand Marlborough Sauvignon Blanc. We would like the packaging will portray elegance and style with an understated label. We are looking for a label that portrays the elegance of the French Riviera. The label should be round or pill shaped.
Updates

Industry/Entity Type

Wine

Font styles to use
Serif
Sans Serif

Requirements
Must have
• The words in order of importance: Dunmore Vale, Sauvignon Blanc, Marlborough, New Zealand. It should be fit to the bottle posted in the links
Nice to have
• a pill shape or circular shape
Should not have
• Illustrations of wine bottles, wine glasses, or grapes

```html
<!DOCTYPE html>
<html lang="en">
<head>
<meta charset="utf-8">
<title>Dunmore Vale Sauvignon Blanc Label</title>
<link rel="stylesheet" href="https://fonts.googleapis.com/css2?family=Italiana&family=Gilda+Display&display=swap">
<style>
  :root {
    --page: #ffffff;
    --frame: #cdd33f;
    --label: #ffffff;
    --ink: #111111;
    --varietal: #8ea52a;
    --art-yellow: #e6dc1a;
    --art-green: #a4c234;
    --art-dark: #5d6b1e;
  }
  * { margin: 0; padding: 0; box-sizing: border-box; }
  html, body {
    width: 1200px;
    height: 675px;
    overflow: hidden;
    background: var(--page);
  }
  .canvas {
    position: relative;
    width: 1200px;
    height: 675px;
  }
  .label {
    position: absolute;
    left: 420px;
    top: 74px;
    width: 360px;
    height: 526px;
    border-radius: 180px;
    background: var(--frame);
  }
  .label-field {
    position: absolute;
    left: 19px;
    top: 19px;
    right: 19px;
    bottom: 19px;
    border-radius: 161px;
    background: var(--label);
  }
  .brand-dot {
    position: absolute;
    left: 50%;
    top: 44px;
    width: 18px;
    height: 18px;
    margin-left: -9px;
    border-radius: 50%;
    background: var(--frame);
  }
  .brand-name {
    position: absolute;
    left: 0;
    right: 0;
    top: 96px;
    text-align: center;
    font-family: "Italiana", "Gilda Display", serif;
    font-size: 52px;
    line-height: 48px;
    letter-spacing: 1px;
    text-transform: uppercase;
    color: var(--ink);
  }
  .varietal {
    position: absolute;
    left: 0;
    right: 0;
    top: 204px;
    text-align: center;
    font-family: "Gilda Display", serif;
    font-size: 30px;
    color: var(--varietal);
  }
  .origin {
    position: absolute;
    left: 0;
    right: 0;
    top: 254px;
    text-align: center;
    font-family: "Gilda Display", serif;
    font-size: 18px;
    color: var(--ink);
  }
  .origin .sep { margin: 0 8px; font-size: 12px; vertical-align: 2px; }
  .emblem {
    position: absolute;
    left: 82px;
    top: 296px;
    width: 194px;
    height: 220px;
  }
</style>
</head>
<body>
<main class="canvas">
  <section class="label">
    <div class="label-field"></div>
    <span class="brand-dot"></span>
    <h1 class="brand-name">Dunmore<br>Vale</h1>
    <p class="varietal">Sauvignon Blanc</p>
    <p class="origin">Marlborough<span class="sep">&#9679;</span>New Zealand</p>
    <svg class="emblem" viewBox="0 0 194 220" role="img" aria-label="Decorative Pacific-style spiral pattern crowned with yellow and green frangipani flowers">
      <defs>
        <linearGradient id="emblem-tone" x1="0" y1="0" x2="0" y2="1">
          <stop offset="0" stop-color="var(--art-yellow)"/>
          <stop offset="0.45" stop-color="var(--art-green)"/>
          <stop offset="1" stop-color="var(--art-dark)"/>
        </linearGradient>
      </defs>
      <path d="M40 0 C80 0 95 18 120 16 C150 14 175 30 180 60 C194 90 194 150 170 185 C150 212 120 220 97 220 C60 220 25 205 10 170 C-2 140 0 100 10 70 C8 40 15 5 40 0 Z" fill="var(--frame)"/>
      <ellipse cx="97" cy="138" rx="82" ry="78" fill="url(#emblem-tone)"/>
    </svg>
  </section>
</main>
</body>
</html>
```